Melvane Home Page

I want to design a new home page using the look of two pages that I like.
http://us.trossini-example.com/
http://www.vellmont-example.us/?cm_mmc=seeker-_-EG_BR_Vellmont_Exact_VLM_D-_-Search-_-vellmonthttp://us.trossini-example.com/
I like the framing of the trossini site and the drop down feel of the vellmont site. I will provide a new logo later today but for now can use what is already on my home page. The pictures in the middle of the page will rotate but I like the fonts and framing from Trossini.
My current site is www.melvane-example.com and I had a designer do a file which came close but missed the mark attached. This upscale and elegant
I liek the top log but would want the glass tilted to look liek the rest of the letters and in a grey or silver elegant color.
Target Market(s)
High end individuals andn corporations

```html
<!DOCTYPE html>
<html lang="en">
<head>
<meta charset="utf-8">
<title>Melvane — Travel</title>
<link rel="stylesheet" href="https://fonts.googleapis.com/css2?family=Old+Standard+TT:wght@400&display=swap">
<style>
  :root {
    --ink: #ffffff;
    --muted: #a8adb2;
    --header-veil: rgba(20, 22, 24, 0.55);
    --nav-veil: rgba(12, 14, 16, 0.72);
    --rule: rgba(255, 255, 255, 0.28);
    --footer-bg: #050505;
    --sky-light: #c9d6dc;
    --sky-mid: #1f6f86;
    --sky-deep: #0b2c3c;
    --sky-edge: #02080c;
    --dot-off: #8a8a8a;
    --social: #5d6166;
  }
  * { margin: 0; padding: 0; box-sizing: border-box; }
  html, body {
    width: 1200px; height: 900px; overflow: hidden;
    background: var(--footer-bg);
    font-family: "Old Standard TT", "Century Schoolbook", Georgia, serif;
    color: var(--ink);
  }
  .page { position: relative; width: 1200px; height: 900px; }

  .hero-photo {
    position: absolute; left: 0; top: 0; width: 1200px; height: 745px;
    background:
      radial-gradient(ellipse 330px 240px at 430px 250px, var(--sky-light) 0%, rgba(160,190,200,0.55) 40%, transparent 100%),
      radial-gradient(ellipse 700px 520px at 520px 420px, var(--sky-mid) 0%, var(--sky-deep) 60%, var(--sky-edge) 100%);
  }

  .site-header {
    position: absolute; left: 0; top: 0; width: 1200px; height: 135px;
    background: var(--header-veil);
    border-bottom: 1px solid var(--rule);
  }
  .brand {
    position: absolute; left: 42px; top: 38px;
    font-size: 52px; line-height: 1; letter-spacing: 1px;
  }
  .header-divider {
    position: absolute; left: 335px; top: 28px; width: 1px; height: 77px;
    background: var(--rule);
  }
  .utility-links {
    position: absolute; left: 356px; top: 31px; list-style: none;
    font-size: 14.5px; letter-spacing: 0.5px; line-height: 26px;
  }
  .social-links {
    position: absolute; left: 1178px; top: 20px; list-style: none;
  }
  .social-links li {
    width: 20px; height: 20px; margin-bottom: 4px; background: var(--social);
  }

  .main-nav {
    position: absolute; left: 0; top: 136px; width: 1200px; height: 37px;
    background: var(--nav-veil);
  }
  .main-nav li {
    position: absolute; top: 10px; list-style: none;
    font-size: 14.5px; letter-spacing: 0.4px; color: var(--muted);
  }
  .main-nav li.is-active { color: var(--ink); }

  .hero-title {
    position: absolute; left: 0; width: 1270px; top: 418px; text-align: center;
    font-size: 66px; font-weight: 400; letter-spacing: 1px; line-height: 1;
  }
  .slide-dots { position: absolute; left: 1051px; top: 718px; display: flex; gap: 8px; }
  .slide-dots span { width: 10px; height: 10px; border-radius: 50%; background: var(--dot-off); }
  .slide-dots span.is-current { background: var(--ink); }

  .site-footer {
    position: absolute; left: 0; top: 745px; width: 1200px; height: 155px;
    background: var(--footer-bg); text-align: center;
  }
  .service-summary {
    position: absolute; left: 0; width: 1245px; top: 23px;
    font-size: 18px; line-height: 23px; letter-spacing: 0.3px;
  }
  .copyright {
    position: absolute; left: 0; width: 1245px; top: 122px; font-size: 17px;
  }
</style>
</head>
<body>
<div class="page">
  <div class="hero-photo" role="img" aria-label="Photo looking up at a passenger jet crossing a bright cloudy blue sky beside a street lamp"></div>

  <header class="site-header">
    <div class="brand">MELVANE</div>
    <div class="header-divider"></div>
    <ul class="utility-links">
      <li>MEMBER LOGIN</li>
      <li>JOIN OUR ENTOURAGE</li>
      <li>CONTACT US</li>
    </ul>
    <ul class="social-links" aria-label="Social links">
      <li></li><li></li><li></li><li></li>
    </ul>
  </header>

  <nav class="main-nav">
    <ul>
      <li style="left:42px">ENTOURAGE &amp; STAFFING</li>
      <li style="left:280px">EVENTS</li>
      <li class="is-active" style="left:390px">TRAVEL</li>
      <li style="left:498px">CELEBRITY &amp; PR</li>
      <li style="left:672px">OTHER SERVICES</li>
      <li style="left:848px">CLIENTS</li>
    </ul>
  </nav>

  <h1 class="hero-title">TRAVEL.</h1>
  <div class="slide-dots">
    <span class="is-current"></span><span></span><span></span><span></span><span></span><span></span>
  </div>

  <footer class="site-footer">
    <p class="service-summary">LUXURY VILLAS, YACHTS, PRIVATE AIR TRAVEL, TOP HOTELS,<br>CORPORATE AND GROUP TRAVEL</p>
    <p class="copyright">Copyright © Melvane LLC 2014.</p>
  </footer>
</div>
</body>
</html>
```